Advanced Therapeutic Massage Therapist

I need a business card advertising my massage services as an advanced therapeutic massage therapist. I offer advanced therapeutic massage, swedish and deep tissue. I want to create a simple, professional and feminine card. I like bright colours and creativity.

I prefer a bold and experimental approach rather than something status-quo. A card to suggest therapeutic healing through dynamic massage. Motifs, shapes or layout which suggest movement and flow.
Updates

Target Market(s)

Everybody!

Industry/Entity Type

Health And Wellness

Contact Information for Business Card

The card should include:
My name, logo, services offered and my contact details.

Sláine Dunleavy
Massage Therapist

- Swedish - Deep Tissue - Advanced Therapeutic

Phone: (+353) 87 216 4093
Email: regenerate@slainedunleavy-example.com
Website: www.slainedunlevy-example.com

Font styles to use
Serif
Sans Serif
Decorative
Script

Colors

Designer to choose colors to be used in the design.

Requirements
Must have
• An example may contain something like this, yet concise:
• "Sláine Dunleavy
• Massage Therapist
• - Swedish - Deep Tissue - Advanced Therapeutic"
Nice to have
• This sentence is optional:
• Imagery such as a logo or symbol. I have attached a file containing a logo I had produced however the name is incorrect now as it is "Sláine" not "Nelly". It could be edited to change it to Sláine.
• I have sent the file as .psd .jpg. .pdf and .png
• I like when the card conveys energy, movement, pressure points, flow etc.
• I just like the designer to follow their own style and ideas. I like bright colours but must have a lot of a base colour to offset it. I really prefer them to follow their own inspiration. That is my preference.
Should not have
• Pine trees, non-native trees to Britain and Ireland, exotic flowers or animals that are not native to Britain and Ireland.
• I don't like brown as the background colour of the card.
• The cars shouldn't look like a wedding invitation i.e too many floral type designs.

```html
<!DOCTYPE html>
<html lang="en">
<head>
<meta charset="utf-8">
<title>Sláine Dunleavy – Massage Therapist Business Card</title>
<link rel="stylesheet" href="https://fonts.googleapis.com/css2?family=PT+Sans:wght@400;700&family=Great+Vibes&family=Quicksand:wght@400&display=swap">
<style>
  :root {
    --stage: #000000;
    --card: #333437;
    --card-edge: #2c2d30;
    --text: #f2f2f2;
    --muted: #b9b9b9;
    --divider: #46474b;
    --bullet: #c9d7b8;
    --icon: #c98a4a;
    --emblem-light: #bfe6dd;
    --emblem-mid: #8fcfc4;
    --emblem-ring: #8a5a2a;
  }
  * { margin: 0; padding: 0; box-sizing: border-box; }
  html, body {
    width: 1200px; height: 900px; overflow: hidden;
    background: var(--stage);
  }
  .canvas { position: relative; width: 1200px; height: 900px; }
  .card {
    position: absolute; top: 271px;
    width: 457px; height: 281px;
    border-radius: 14px;
    background: linear-gradient(180deg, var(--card) 0%, var(--card-edge) 100%);
  }
  .card--back { left: 137px; }
  .card--front { left: 626px; }

  .emblem {
    position: absolute; width: 140px; height: 140px; border-radius: 50%;
    background: radial-gradient(circle, var(--emblem-light) 0%, var(--emblem-mid) 78%, var(--emblem-ring) 88%, var(--card) 100%);
  }
  .card--back .emblem { left: 55px; top: 67px; }
  .card--front .emblem { left: 159px; top: 54px; }

  .divider {
    position: absolute; left: 226px; top: 84px;
    width: 1px; height: 126px; background: var(--divider);
  }
  .contact { position: absolute; left: 243px; top: 85px; list-style: none; }
  .contact li {
    display: flex; align-items: center; gap: 7px;
    font: 400 13px/19px "PT Sans", sans-serif; color: var(--text);
  }
  .contact svg { width: 10px; height: 10px; fill: var(--icon); }

  .services { position: absolute; left: 244px; top: 140px; list-style: none; }
  .services li {
    display: flex; align-items: center; gap: 4px;
    font: 700 13px/19px "PT Sans", sans-serif; color: var(--text);
  }
  .services li::before {
    content: ""; width: 8px; height: 8px; border-radius: 50%;
    background: var(--bullet);
  }

  .identity {
    position: absolute; left: 0; width: 100%; top: 195px;
    text-align: center;
  }
  .identity__name {
    font: 400 27px/1 "Great Vibes", cursive; color: var(--text);
  }
  .identity__role {
    margin-top: -2px;
    font: 400 11px/1 "Quicksand", sans-serif; letter-spacing: 1px;
    color: var(--muted);
  }
</style>
</head>
<body>
<main class="canvas">
  <section class="card card--back">
    <div class="emblem" role="img" aria-label="Circular emblem with an ornamental tree in copper on soft turquoise"></div>
    <div class="divider"></div>
    <ul class="contact">
      <li>
        <svg viewBox="0 0 10 10" aria-hidden="true"><path d="M2 0.5 L3.6 2.6 L2.6 3.7 Q3.6 5.9 6.3 7.4 L7.4 6.4 L9.5 8 L8.3 9.5 Q4.5 9.2 2 6.3 Q0.4 4 0.6 1.5 Z"/></svg>
        (+353) 87 216 4093
      </li>
      <li>
        <svg viewBox="0 0 10 10" aria-hidden="true"><rect x="0.5" y="2" width="9" height="6.5"/><path d="M0.5 2 L5 5.6 L9.5 2" fill="none" stroke="#333437" stroke-width="0.9"/></svg>
        slainemassage@example.com
      </li>
    </ul>
    <ul class="services">
      <li>Swedish</li>
      <li>Deep Tissue</li>
      <li>Advanced Therapeutic</li>
    </ul>
  </section>

  <section class="card card--front">
    <div class="emblem" role="img" aria-label="Circular emblem with an ornamental tree in copper on soft turquoise"></div>
    <div class="identity">
      <p class="identity__name">Sláine Dunleavy</p>
      <p class="identity__role">massage therapist</p>
    </div>
  </section>
</main>
</body>
</html>
```